Gaming company needs web presence

PLEASE NOTE: We need just a simple web site. We are at least a year away from launching our first product, so the site only needs a small amount of information on it. The only people who will be visiting the web site are prospective employees, prospective investors who want a little information on the company, journalists who want a little more information, and people in the games industry who will visit to read blog posts about the development of our first game.

Lanternfield Games is a new gaming company that wants to change how people think about video games. We are making games that we think can be so interesting to watch that people might want to tune into them instead of the TV.

The games we make are sophisticated, they are not for children, and we want to project an image of being serious about our craft and the brand we're trying to create. Our games are heavily focused on players interacting with each other in sophisticated ways: to negotiate, to compete, to fight, to come to each other's rescue, to cheer each other on, or to simply watch each other in awe.

We do not want a site that features lots of video game cliches like joysticks, 8 bit graphics, science fiction themes, or military themes. We are focused on craftsmanship, so we'd like to project a sense of precision, pride and deep purpose.

The purpose of this website is to create an image of our company that can help us recruit like-minded craftspeople and help find business partners. There will be no e-commerce, account creation, or forums for some time. The site should have:
-A front page that describes our business
-A section that describes our first game (we have only one for now)
-A section for employees to write blog posts. There should be something on the home page that shows links to the latest 3 blog posts.
-A section about founders that shows information about them.
-Contact information, lets people send us email

Our first game is one that looks very realistic. It takes place on a tropical island. We can't say a lot more about it in public yet, but I will say these things: it is not a game that children will play, it is not very violent, it would look more like a film than a typical video game.

And the site should be easily extendable when we have more content and more categories of content.

I've attached our official company logo with a color scheme we've been using, plus an alternate version of the logo. Please use this as a starting point for the web site's visual design. Also, I do not think it is necessary to use the dark background in the logo as the background throughout the site. I wouldn't rule it out, but I'd like to see some proposals with lighter backgrounds.

We need to be able to get code from you so that we can drop it on our server and get it running without extra effort. We need to be able to add content for Blog posts easily as well, so please indicate how that would work.
Updates

Hello everyone, Thanks for all of the great submissions so far. There are some important things I'd like to relay to everyone: We are at least a year away from launching our first game, so we only need a simple web site. Unfortunately, we can't share any screenshots or details about our first game yet. All of these submissions look great, but are far too complicated. Also, I really want to stress that we don't want to feature stock photography of people playing games, especially of children playing games. In fact, since we don't want to release any screenshots of our games and we don't have any good photography of ourselves working, it's best if there are no photographic images on the site for now.

Hello designers, Can you let me know if your designs include all the code that would let us drop the files on to our web server and easily get it up and running? Also, can you tell me how the blog posts would be created? Does your code run on a CMS? Thanks, Haskell

Hi Designers, we will be hosting this site with Wordpress, so we would prefer to have submissions ready to go on a Wordpress server. Thanks!

Target Market(s)

Investors, prospective employees, press, blog post readers.

Industry/Entity Type

Business

Font styles to use
Sans Serif

Requirements
Must have
• Simplicity first. Please use a color palette and fonts that match our logo.
Should not have
• Video game cliches. Flash animations or menus.
No children.
No photographs of people playing games.

(I realize this is very limiting, but we're keeping the sits as simple as possible for now)

```html
<!DOCTYPE html>
<html lang="en">
<head>
<meta charset="utf-8">
<title>Lanternfield Games</title>
<link rel="stylesheet" href="https://fonts.googleapis.com/css2?family=Open+Sans:wght@300;400;600;700;800&family=Arvo:wght@700&display=swap">
<style>
  :root{
    --bark:#3f2211;
    --wood:#5b3219;
    --wood-light:#70401f;
    --ember:#e47f35;
    --ember-deep:#c9682a;
    --parchment:#f6f0d8;
    --parchment-deep:#ece3c2;
    --ink:#5a3a22;
    --muted:#8a7560;
    --white:#ffffff;
    --field:#ffffff;
    --field-line:#ddd2b0;
  }
  *{box-sizing:border-box;margin:0;padding:0}
  html,body{width:841px;height:1200px;overflow:hidden}
  body{font-family:"Open Sans",sans-serif;color:var(--ink);background:var(--white);position:relative}

  /* Hero */
  .hero{position:absolute;left:0;top:0;width:841px;height:392px;
    background:radial-gradient(ellipse at 50% 55%,var(--wood-light) 0%,var(--wood) 55%,var(--bark) 100%)}
  .hero::after{content:"";position:absolute;left:50%;bottom:-18px;transform:translateX(-50%);
    border-left:20px solid transparent;border-right:20px solid transparent;border-top:18px solid var(--bark);z-index:2}
  .brand{position:absolute;left:112px;top:36px;color:var(--white);font-weight:800;line-height:1;letter-spacing:.5px}
  .brand .name{font-size:22px;display:block}
  .brand .sub{font-size:14px;display:block;margin-top:3px;letter-spacing:2px}
  .social-top{position:absolute;right:114px;top:34px;display:flex;gap:5px}
  .social-top span{width:11px;height:11px;border-radius:50%;background:var(--white);display:block;opacity:.85}
  .nav{position:absolute;right:114px;top:64px;display:flex;gap:20px;list-style:none}
  .nav li{color:var(--white);font-size:9px;font-weight:600;letter-spacing:.4px}

  .tagline{position:absolute;left:0;top:146px;width:841px;height:140px;font-family:"Arvo",serif;text-transform:uppercase}
  .tagline .we-are{position:absolute;left:0;width:841px;top:0;text-align:center;color:var(--ember);font-size:15px;letter-spacing:2px}
  .tagline .row{position:absolute;font-size:29px;letter-spacing:1.5px}
  .tagline .l1{color:var(--parchment-deep);right:488px;top:38px}
  .tagline .r1{color:var(--parchment-deep);left:486px;top:38px}
  .tagline .l2{color:var(--ember);right:488px;top:78px;font-size:24px}
  .tagline .r2{color:var(--ember);left:486px;top:78px;font-size:24px}
  .emblem{position:absolute;left:358px;top:164px;width:124px;height:124px;border-radius:50%;background:var(--ember)}
  .divider{position:absolute;left:370px;top:296px;width:100px;height:6px}

  /* Process */
  .process{position:absolute;left:0;top:392px;width:841px;height:156px;background:var(--parchment)}
  .steps{position:absolute;left:110px;top:36px;width:621px;height:100px}
  .step{position:absolute;top:0;width:90px;text-align:center}
  .step svg{display:block;margin:0 auto}
  .step .label{display:block;margin-top:12px;font-size:9px;font-weight:600;letter-spacing:.5px;color:var(--ink)}
  .connector{position:absolute;top:20px;height:2px;border-top:1px dashed #c9b994}
  .connector::after{content:"";position:absolute;left:50%;top:-4px;width:6px;height:6px;border-radius:50%;background:#c9b994;transform:translateX(-50%)}

  /* Welcome */
  .welcome{position:absolute;left:0;top:548px;width:841px;height:200px;text-align:center}
  .section-title{font-weight:300;font-size:22px;letter-spacing:.5px;color:var(--ink)}
  .welcome .section-title{margin-top:70px}
  .welcome p{width:600px;margin:10px auto 0;font-size:8px;line-height:13px;color:var(--muted)}

  /* Games + blog */
  .games{position:absolute;left:123px;top:772px;width:388px}
  .blogs{position:absolute;left:538px;top:772px;width:184px}
  .col-title{font-size:12px;font-weight:600;color:var(--ink);padding-bottom:6px;border-bottom:2px solid var(--parchment-deep);position:relative}
  .col-title::after{content:"";position:absolute;left:0;bottom:-2px;width:60px;height:2px;background:var(--ember)}
  .tiles{display:flex;gap:6px;margin-top:12px}
  .tile{width:125px;height:140px;border-radius:2px}
  .tile.one{background:linear-gradient(160deg,#3d2a5e,#b08a2a)}
  .tile.two{background:linear-gradient(160deg,#2f5fa8,#d0622f)}
  .tile.three{background:linear-gradient(160deg,#5a3a2a,#2a1e18)}
  .post{display:flex;gap:8px;margin-top:12px;padding-bottom:10px;border-bottom:1px solid var(--parchment-deep)}
  .post .thumb{width:60px;height:46px;flex:none}
  .post .thumb.a{background:linear-gradient(135deg,#7a2f1e,#d07a3a)}
  .post .thumb.b{background:linear-gradient(135deg,#3b2a22,#9a6a44)}
  .post h4{font-size:8px;font-weight:700;color:var(--ember);letter-spacing:.3px}
  .post .meta{font-size:7px;color:var(--muted);margin-top:4px;line-height:11px}

  /* Contact */
  .contact{position:absolute;left:0;top:966px;width:841px;height:168px;background:var(--parchment);text-align:center}
  .contact .section-title{margin-top:16px}
  .contact p{width:520px;margin:6px auto 0;font-size:7.5px;line-height:11px;color:var(--muted)}
  .form{position:absolute;left:142px;top:74px;width:558px;height:80px}
  .field{position:absolute;background:var(--field);border:1px solid var(--field-line);height:16px;font-size:7px;color:var(--muted);text-align:left;padding:3px 6px}
  .field.name{left:0;top:0;width:260px}
  .field.email{left:0;top:22px;width:260px}
  .field.reason{left:0;top:44px;width:260px}
  .field.message{left:278px;top:0;width:280px;height:38px}
  .send{position:absolute;left:278px;top:44px;width:280px;height:16px;background:var(--ember);color:var(--white);font-size:7px;font-weight:700;letter-spacing:1px;text-align:center;line-height:16px}

  /* Footer */
  .footer{position:absolute;left:0;top:1134px;width:841px;height:66px;background:var(--bark)}
  .footer .brand{left:123px;top:16px}
  .footer .brand .name{font-size:16px}
  .footer .brand .sub{font-size:10px}
  .legal{position:absolute;left:470px;top:29px;font-size:7px;color:var(--parchment-deep)}
  .social-foot{position:absolute;left:640px;top:27px;display:flex;gap:9px}
  .social-foot span{width:10px;height:10px;border-radius:50%;background:var(--parchment-deep);display:block}
</style>
</head>
<body>

<header class="hero">
  <div class="brand"><span class="name">LANTERNFIELD</span><span class="sub">GAMES</span></div>
  <div class="social-top"><span></span><span></span><span></span><span></span></div>
  <ul class="nav">
    <li>HOME</li><li>ABOUT US</li><li>SERVICES</li><li>BLOG</li><li>REVIEWS</li><li>CONTACT US</li>
  </ul>

  <div class="tagline">
    <div class="we-are">We Are</div>
    <div class="row l1">Craftsmen of</div>
    <div class="row r1">Beautifully</div>
    <div class="row l2">Best Gaming</div>
    <div class="row r2">Experiences</div>
  </div>
  <div class="emblem"></div>
  <svg class="divider" viewBox="0 0 100 6">
    <line x1="0" y1="3" x2="38" y2="3" stroke="#e47f35" stroke-width="1"/>
    <circle cx="44" cy="3" r="2" fill="#e47f35"/>
    <circle cx="50" cy="3" r="2" fill="#e47f35"/>
    <circle cx="56" cy="3" r="2" fill="#e47f35"/>
    <line x1="62" y1="3" x2="100" y2="3" stroke="#e47f35" stroke-width="1"/>
  </svg>
</header>

<section class="process">
  <div class="steps">
    <div class="step" style="left:0">
      <svg width="40" height="40" viewBox="0 0 40 40" fill="none" stroke="#e47f35" stroke-width="2">
        <circle cx="17" cy="17" r="10"/><line x1="24" y1="24" x2="34" y2="34"/>
      </svg>
      <span class="label">DISCOVER</span>
    </div>
    <div class="connector" style="left:80px;width:100px"></div>
    <div class="step" style="left:170px">
      <svg width="40" height="40" viewBox="0 0 40 40" fill="none" stroke="#e47f35" stroke-width="2">
        <line x1="8" y1="32" x2="32" y2="8"/><line x1="8" y1="8" x2="32" y2="32"/>
        <polygon points="5,35 8,27 13,32"/>
      </svg>
      <span class="label">DESIGN</span>
    </div>
    <div class="connector" style="left:250px;width:110px"></div>
    <div class="step" style="left:350px">
      <svg width="40" height="40" viewBox="0 0 40 40" fill="none" stroke="#e47f35" stroke-width="2">
        <rect x="4" y="7" width="32" height="21" rx="1"/><line x1="20" y1="28" x2="20" y2="34"/><line x1="12" y1="34" x2="28" y2="34"/>
      </svg>
      <span class="label">DEVELOP</span>
    </div>
    <div class="connector" style="left:430px;width:110px"></div>
    <div class="step" style="left:531px">
      <svg width="40" height="40" viewBox="0 0 40 40" fill="none" stroke="#e47f35" stroke-width="2">
        <line x1="8" y1="32" x2="32" y2="8"/><polyline points="18,8 32,8 32,22"/>
      </svg>
      <span class="label">DEPLOY</span>
    </div>
  </div>
</section>

<section class="welcome">
  <h2 class="section-title">WELCOME TO LANTERNFIELD GAMES</h2>
  <p>Lanternfield Games is a young studio building games that are as rewarding to watch as they are to play. We care about craft, precision and the small details that make a world feel alive. Our team works slowly and deliberately, shaping every system around the ways players meet, bargain, compete and help one another.</p>
  <p>We are still early in the journey, and we share our progress openly on the studio blog.</p>
</section>

<section class="games">
  <h3 class="col-title">OUR NEW GAMES</h3>
  <div class="tiles">
    <div class="tile one" role="img" aria-label="Game cover artwork"></div>
    <div class="tile two" role="img" aria-label="Game cover artwork"></div>
    <div class="tile three" role="img" aria-label="Game cover artwork"></div>
  </div>
</section>

<aside class="blogs">
  <h3 class="col-title">RECENT BLOGS</h3>
  <article class="post">
    <div class="thumb a" role="img" aria-label="Blog post thumbnail"></div>
    <div><h4>STUDIO NOTES</h4><div class="meta">Posted by Haskell<br>4 Comments</div></div>
  </article>
  <article class="post">
    <div class="thumb b" role="img" aria-label="Blog post thumbnail"></div>
    <div><h4>FIELD JOURNAL</h4><div class="meta">Posted by Haskell<br>4 Comments</div></div>
  </article>
</aside>

<section class="contact">
  <h2 class="section-title">CONTACT US</h2>
  <p>Whether you are a craftsperson hoping to join us, an investor or a journalist, we would be glad to hear from you. Write to us below.</p>
  <div class="form">
    <div class="field name">Name</div>
    <div class="field email">Email Address</div>
    <div class="field reason">Enquiry Reason</div>
    <div class="field message">Contact Number</div>
    <div class="send">SEND</div>
  </div>
</section>

<footer class="footer">
  <div class="brand"><span class="name">LANTERNFIELD</span><span class="sub">GAMES</span></div>
  <div class="legal">© 2015 All Rights Reserved &nbsp;|&nbsp; Privacy Policy</div>
  <div class="social-foot"><span></span><span></span><span></span><span></span></div>
</footer>

</body>
</html>
```